Redesign website for small print company

Vindurgata is a small printing company in Iceland mainly servicing Students, schools, etc. We are also doing all kind of other jobs, like business cards, book printing, brochure printing etc. We are also selling books online.
Our website is: www.vindurgata.is
What we are looking for is:
- Web Design (Uncoded - PSD layout only)
- Mobile friendly design, using our current color scheme: Red, green, yellow and light gray.
- Clean simple design
- Simple, light and easy to use.
- More menu Items/drop down
Industry/Entity Type
Digital Printing
Number of Pages Required
5+ page
Requirements
Must have
- Easy navigation
- Designed for mobile
- Current color scheme (see logo)
Nice to have
- Icon based products

```html
<!DOCTYPE html>
<html lang="en">
<head>
<meta charset="utf-8">
<title>Vindurgata — Printing Services</title>
<link href="https://fonts.googleapis.com/css2?family=Poppins:wght@400;500;600;700&display=swap" rel="stylesheet">
<style>
:root{
  --red:#ef3b33;
  --red-dark:#d9302a;
  --green:#1f6b3a;
  --yellow:#f6d20f;
  --ink:#1b1b1b;
  --text:#444;
  --light:#f1f1f1;
  --card:#e9eaec;
  --footer:#222;
  --footer-text:#d8d8d8;
}
*{box-sizing:border-box;margin:0;padding:0}
html,body{width:1200px;height:3536px;overflow:hidden}
body{font-family:"Poppins",sans-serif;color:var(--ink);background:#fff;position:relative}
a{color:inherit;text-decoration:none}

/* Header */
.site-header{height:113px;position:relative;background:#fff}
.brand{position:absolute;left:96px;top:28px;display:flex;align-items:center;gap:14px}
.brand-mark{width:50px;height:58px;background:var(--red)}
.brand-name{font-size:38px;font-weight:700;color:var(--ink);letter-spacing:.5px}
.main-nav{position:absolute;right:90px;top:38px;display:flex;align-items:center;gap:26px;font-size:16px;white-space:nowrap}
.main-nav .active{border:2px solid var(--red);padding:4px 10px;color:var(--ink)}
.main-nav .active::after{content:" ▾";font-size:10px;color:var(--red)}
.nav-tools{display:flex;gap:16px;align-items:center;color:var(--red)}
.nav-sep{width:1px;height:18px;background:var(--red)}

/* Dropdown */
.dropdown{height:170px;background:var(--red);display:grid;grid-template-columns:350px 310px 300px;padding:40px 0 0 178px;row-gap:22px}
.dropdown a{color:#fff;font-size:24px;display:flex;align-items:center;gap:14px;white-space:nowrap}
.dropdown svg{width:26px;height:26px}

/* Hero */
.hero{height:408px;position:relative;background:linear-gradient(120deg,#3a342e,#6b5f52 45%,#2c2a28);overflow:hidden}
.hero-photo{position:absolute;inset:0;background:radial-gradient(ellipse at 45% 60%,rgba(190,160,130,.45),transparent 60%)}
.hero h1{position:absolute;top:30px;width:100%;text-align:center;color:#fff;font-size:58px;font-weight:700;line-height:72px}
.hero-arrow{position:absolute;top:97px;width:46px;height:46px;border-radius:50%;display:flex;align-items:center;justify-content:center;color:#fff;font-size:22px}
.hero-arrow.prev{left:25px;background:#1b1b1b}
.hero-arrow.next{right:25px;background:var(--red)}

/* Services strip */
.services{height:216px;display:flex;border-bottom:8px solid var(--ink)}
.services-intro{width:332px;background:var(--red);color:#fff;padding:30px 0 0 94px}
.services-intro h2{font-size:36px;font-weight:700;margin-bottom:14px}
.services-intro p{font-size:15px;line-height:25px;width:220px}
.service{flex:1;display:flex;flex-direction:column;align-items:center;padding-top:44px;position:relative}
.service svg{width:90px;height:90px}
.service span{margin-top:20px;font-size:16px;font-weight:600;white-space:nowrap}
.service::after{content:"";position:absolute;left:0;right:0;bottom:-8px;height:8px}
.service.s1 span{color:var(--red)} .service.s1::after{background:var(--yellow)}
.service.s2 span{color:var(--green)} .service.s2::after{background:var(--green)}
.service.s3 span{color:var(--red)} .service.s3::after{background:var(--red)}
.service.s4 span{color:var(--ink)} .service.s4::after{background:var(--ink)}

/* Catalog */
.catalog{text-align:center;padding-top:72px;height:889px}
.section-title{color:var(--red);font-size:38px;font-weight:700;white-space:nowrap}
.catalog .lead{font-size:17px;line-height:30px;color:var(--text);width:660px;margin:18px auto 0}
.catalog-grid{display:flex;gap:28px;justify-content:center;margin-top:50px}
.catalog-card{width:306px}
.catalog-img{height:347px;background:var(--card);display:flex;align-items:center;justify-content:center;position:relative}
.catalog-img svg{width:170px;height:170px}
.tricolor{height:8px;display:flex}
.tricolor i{flex:1}
.tricolor i:nth-child(1){background:var(--yellow)}
.tricolor i:nth-child(2){background:var(--green)}
.tricolor i:nth-child(3){background:var(--red)}
.catalog-card h3{color:var(--red);font-size:26px;font-weight:700;margin-top:30px}
.btn{display:inline-block;background:var(--red);color:#fff;font-weight:600;font-size:18px;border-radius:32px;padding:18px 44px}
.catalog .btn{margin-top:60px}

/* Welcome */
.welcome{height:443px;background:var(--light);text-align:center;padding-top:60px}
.welcome p{width:900px;margin:24px auto 0;font-size:16.5px;line-height:30px;color:var(--text)}
.welcome .btn{margin-top:22px;padding:16px 46px}

/* Gallery */
.gallery{height:632px;position:relative}
.gallery .section-title{position:absolute;left:94px;top:66px}
.filters{position:absolute;left:94px;top:165px;list-style:none;font-size:19px;color:#555;width:210px}
.filters li{height:47px;line-height:47px;padding-left:16px;margin-bottom:16px;white-space:nowrap}
.filters li.active{background:var(--red);color:#fff;font-weight:600;width:125px}
.gallery-grid{position:absolute;left:328px;top:177px;width:872px;height:370px;display:grid;grid-template-columns:repeat(3,1fr);grid-template-rows:1fr 1fr;gap:2px}
.tile.t1{background:linear-gradient(135deg,#e8cfd8,#c9d6de)}
.tile.t2{background:linear-gradient(135deg,#d7dad6,#6f8a7a)}
.tile.t3{background:linear-gradient(135deg,#6f7f90,#c8b59a)}
.tile.t4{background:linear-gradient(135deg,#d9d7d2,#5a5e66)}
.tile.t5{background:linear-gradient(135deg,#ecebe6,#a58f6f)}
.tile.t6{background:linear-gradient(135deg,#8d96a3,#d6c3a7)}

/* Delivery */
.delivery{height:297px;background:var(--light);display:flex;justify-content:center;gap:22px;padding-top:74px}
.delivery-item{width:200px;text-align:center;font-size:17px;line-height:26px;color:#333;white-space:nowrap}
.delivery-item .circle{width:110px;height:110px;border-radius:50%;margin:0 auto 20px;display:flex;align-items:center;justify-content:center}
.delivery-item svg{width:54px;height:54px}
.c-yellow{background:var(--yellow)} .c-green{background:var(--green)} .c-red{background:var(--red)} .c-black{background:var(--ink)}

/* Footer */
.site-footer{height:368px;background:var(--footer);color:var(--footer-text);position:relative}
.footer-col{position:absolute;top:36px;font-size:14.5px;white-space:nowrap}
.footer-col h4{color:#fff;font-size:20px;font-weight:600;margin-bottom:26px}
.footer-col li{list-style:none;height:32px}
.footer-col.divided{border-right:1px solid #444;padding-right:40px;height:240px}
.social{display:flex;gap:8px}
.social span{width:30px;height:30px;border:2px solid #fff;border-radius:50%}
.payments{display:flex;gap:4px;margin-top:58px}
.payments span{width:32px;height:18px;background:#cfd8e4;border-radius:2px}
.footer-bottom{position:absolute;left:94px;right:94px;top:285px;border-top:1px solid #3a3a3a;text-align:center;padding-top:26px;font-size:15px}
</style>
</head>
<body>

<header class="site-header">
  <a class="brand" href="#"><span class="brand-mark"></span><span class="brand-name">Vindurgata</span></a>
  <nav class="main-nav">
    <a href="#">Home</a>
    <a href="#" class="active">Services</a>
    <a href="#">Submission of Works</a>
    <a href="#">About Us</a>
    <span class="nav-tools">
      <svg width="18" height="18" viewBox="0 0 20 20" fill="none" stroke="currentColor" stroke-width="2.5"><circle cx="8" cy="8" r="6"/><path d="M13 13l5 5"/></svg>
      <span class="nav-sep"></span>
      <svg width="16" height="18" viewBox="0 0 16 18" fill="currentColor"><path d="M1 5h14v13H1z"/><path d="M5 5V3a3 3 0 016 0v2" fill="none" stroke="currentColor" stroke-width="2"/></svg>
    </span>
  </nav>
</header>

<nav class="dropdown">
  <a href="#"><svg viewBox="0 0 24 24" fill="none" stroke="#fff" stroke-width="1.6"><path d="M5 2h10l4 4v16H5z"/><path d="M8 10h8M8 14h8M8 18h5"/></svg>Essays</a>
  <a href="#"><svg viewBox="0 0 24 24" fill="none" stroke="#fff" stroke-width="1.6"><path d="M4 4l6 2 4-2 6 2v15l-6-2-4 2-6-2z"/><path d="M10 6v15M14 4v15"/></svg>Pamphlets</a>
  <a href="#"><svg viewBox="0 0 24 24" fill="none" stroke="#fff" stroke-width="1.6"><path d="M3 6h18v10H3zM12 16v6M8 22h8M12 2v4"/></svg>Poster</a>
  <a href="#"><svg viewBox="0 0 24 24" fill="none" stroke="#fff" stroke-width="1.6"><rect x="2" y="5" width="20" height="14"/><circle cx="8" cy="11" r="2"/><path d="M13 10h6M13 14h6M5 16h6"/></svg>Business Cards</a>
  <a href="#"><svg viewBox="0 0 24 24" fill="none" stroke="#fff" stroke-width="1.6"><path d="M5 2h14v20H5z"/><path d="M9 8h6v6H9z"/></svg>Book Printing</a>
  <a href="#"><svg viewBox="0 0 24 24" fill="none" stroke="#fff" stroke-width="1.6"><path d="M4 3h14v18H4z"/><circle cx="13" cy="10" r="3"/><path d="M7 7v10"/></svg>Text Books</a>
</nav>

<section class="hero">
  <div class="hero-photo" role="img" aria-label="Print shop worker inspecting freshly printed sheets on a press"></div>
  <h1>Make A Professional<br>First Impression</h1>
  <span class="hero-arrow prev">‹</span>
  <span class="hero-arrow next">›</span>
</section>

<section class="services">
  <div class="services-intro">
    <h2>Services</h2>
    <p>Online and in store, you can find printing services to help you get the job done</p>
  </div>
  <div class="service s1">
    <svg viewBox="0 0 64 64" fill="none" stroke="#ef3b33" stroke-width="2.5"><path d="M14 10l30-4v50l-30 4z"/><path d="M44 6l6 4v48l-6-2"/><circle cx="29" cy="32" r="9"/><path d="M20 32h18M29 23v18"/></svg>
    <span>Tourist Brochure</span>
  </div>
  <div class="service s2">
    <svg viewBox="0 0 64 64" fill="none" stroke="#1f6b3a" stroke-width="2.5"><rect x="6" y="18" width="52" height="28" rx="2"/><path d="M16 18V8h32v10M16 46v10h32V46"/><circle cx="40" cy="30" r="6"/><path d="M12 26h12"/></svg>
    <span>Digital Printing</span>
  </div>
  <div class="service s3">
    <svg viewBox="0 0 64 64" fill="none" stroke="#ef3b33" stroke-width="2.5"><path d="M8 12h40v40H8z"/><path d="M48 20h8v28a4 4 0 01-8 0"/><path d="M14 20h14v12H14zM32 20h10M32 26h10M14 38h28M14 44h28"/></svg>
    <span>Reports</span>
  </div>
  <div class="service s4">
    <svg viewBox="0 0 64 64" fill="none" stroke="#1b1b1b" stroke-width="2.5"><path d="M12 4h40v56H12z"/><path d="M18 4v56"/><path d="M32 20l8 4v9l-8 4-8-4v-9z"/><path d="M24 46h20"/></svg>
    <span>Book Print</span>
  </div>
</section>

<section class="catalog">
  <h2 class="section-title">Catalog</h2>
  <p class="lead">Lorem ipsum dolor sit amet, consectetur adipiscing elit, sed do eiusmod tempor incididunt ut labore et dolore magna aliqua.</p>
  <div class="catalog-grid">
    <article class="catalog-card">
      <div class="catalog-img"><svg viewBox="0 0 100 100" fill="none" stroke="#f6d20f" stroke-width="3"><rect x="6" y="24" width="88" height="56" rx="4"/><path d="M18 70v-8c0-6 5-9 8-10-4-3-5-12 2-14 7-2 10 8 4 14 4 1 8 4 8 10v8z"/><path d="M52 42h30M52 52h30M52 62h22"/></svg></div>
      <div class="tricolor"><i></i><i></i><i></i></div>
      <h3>Business Cards</h3>
    </article>
    <article class="catalog-card">
      <div class="catalog-img"><svg viewBox="0 0 100 100" fill="none" stroke="#1f6b3a" stroke-width="3.5"><path d="M22 20l28-8v80l-28-8z"/><path d="M50 12l28 8v64l-28 8"/><path d="M28 30v40M42 24v56M60 26v48"/></svg></div>
      <div class="tricolor"><i></i><i></i><i></i></div>
      <h3>Pamphlets</h3>
    </article>
    <article class="catalog-card">
      <div class="catalog-img"><svg viewBox="0 0 100 100" fill="none" stroke="#ef3b33" stroke-width="3"><path d="M14 10h60v70H14z"/><path d="M14 80c0 6 4 8 10 8h60V18"/><circle cx="62" cy="34" r="16"/><path d="M62 28v2M62 34v10M22 24h10M22 36h12M22 48h20"/></svg></div>
      <div class="tricolor"><i></i><i></i><i></i></div>
      <h3>Text Books</h3>
    </article>
  </div>
  <a href="#" class="btn">Show More</a>
</section>

<section class="welcome">
  <h2 class="section-title">Welcome to University</h2>
  <p>University education is a company located in the campus, which has specialized in the service of school staff, as well as providing general public printing.Higher education publishes seminars and first-class textbooks for courses, prints theses for lesson, as well as working on an unprecedented number of smaller pieces for students, teachers and organizations. These include brochures, reports, questionnaires, business cards, books, OCR scanning and more.</p>
  <a href="#" class="btn">Read More</a>
</section>

<section class="gallery">
  <h2 class="section-title">Gallery</h2>
  <ul class="filters">
    <li class="active">All</li>
    <li>Business Cards</li>
    <li>Pamphlets</li>
    <li>Book Printing</li>
    <li>Poster</li>
    <li>Text Books</li>
  </ul>
  <div class="gallery-grid">
    <div class="tile t1" role="img" aria-label="Pastel greeting card set with envelopes"></div>
    <div class="tile t2" role="img" aria-label="Open printed brochure lying flat"></div>
    <div class="tile t3" role="img" aria-label="Standing advertising poster in front of a building"></div>
    <div class="tile t4" role="img" aria-label="Stack of fanned-out magazines"></div>
    <div class="tile t5" role="img" aria-label="Open catalog showing interior layout"></div>
    <div class="tile t6" role="img" aria-label="Pile of glossy printed magazines"></div>
  </div>
</section>

<section class="delivery">
  <div class="delivery-item">
    <div class="circle c-yellow"><svg viewBox="0 0 48 48" fill="none" stroke="#fff" stroke-width="2.5"><path d="M14 14h20v18H14zM34 20h6l4 6v6h-10"/><circle cx="20" cy="34" r="3"/><circle cx="38" cy="34" r="3"/><path d="M4 20h8M6 26h6"/></svg></div>
    Shipping by Courier
  </div>
  <div class="delivery-item">
    <div class="circle c-green"><svg viewBox="0 0 48 48" fill="none" stroke="#fff" stroke-width="2.5"><path d="M6 18l18-12 18 12v22H6z"/><path d="M6 18l18 13 18-13"/><path d="M14 14h20v10"/></svg></div>
    Registered Mail<br>Delivery
  </div>
  <div class="delivery-item">
    <div class="circle c-red"><svg viewBox="0 0 48 48" fill="none" stroke="#fff" stroke-width="2.5"><path d="M6 10h36l2 10H4z"/><path d="M8 20v20h32V20"/><path d="M18 40V28h12v12"/></svg></div>
    Delivery<br>To Service Centers
  </div>
  <div class="delivery-item">
    <div class="circle c-black"><svg viewBox="0 0 48 48" fill="none" stroke="#fff" stroke-width="2.5"><path d="M6 14l12-4 12 4 12-4v26l-12 4-12-4-12 4z"/><path d="M18 10v26M30 14v26"/><circle cx="24" cy="12" r="5" fill="#1b1b1b"/></svg></div>
    Pickup
  </div>
</section>

<footer class="site-footer">
  <div class="footer-col divided" style="left:94px;width:224px">
    <h4>Useful Links</h4>
    <ul><li>Home</li><li>Services</li><li>Submission of Works</li><li>About Us</li></ul>
  </div>
  <div class="footer-col divided" style="left:408px;width:190px">
    <h4>Other Links</h4>
    <ul><li>Privacy Policy</li><li>Customer</li><li>Satisfaction</li><li>Secure Shopping</li><li>Digital Printing</li></ul>
  </div>
  <div class="footer-col" style="left:658px">
    <h4>Support</h4>
    <ul><li>Services</li><li>FAQ</li><li>Terms and concepts</li><li>Privacy Policy</li></ul>
  </div>
  <div class="footer-col" style="left:931px">
    <h4>Stay Connected</h4>
    <div class="social" aria-label="Social networks"><span></span><span></span><span></span></div>
    <div class="payments" aria-label="Accepted payment methods"><span></span><span></span><span></span><span></span><span></span></div>
  </div>
  <div class="footer-bottom">© 2018 Copyrights | All Rights Reserved</div>
</footer>

</body>
</html>
```